Harbourline Electrical Solutions

On one side. LOGO (underneath:) Commercial Industrial Residential

- NAME & CONTACT DETAILS

Marcus T. Hollings
Project Manager

(Cell icon) (441) 555-0187
(Email icon) hlelectricalsolutions@mailvento.com
(Facebook & Instagram icons )@hlelectricalsolutions

Other side: LOGO - underneath ELECTRICAL CONSTRUCTION & MAINTENANCE . LED LIGHTING & AUTOMATION . LIFE SAFETY SYSTEMS (FIRE ALARM / SECURITY) . DATA & COMMUNICATION

```html
<!DOCTYPE html>
<html lang="en">
<head>
<meta charset="utf-8">
<title>Harbourline Electrical Solutions – Business Card</title>
<link rel="stylesheet" href="https://fonts.googleapis.com/css2?family=Lato:wght@400;700&family=Raleway:wght@500;600;700&display=swap">
<style>
  :root {
    --backdrop: #2b2b2b;
    --card-white: #ffffff;
    --brand-teal: #0f5468;
    --text-grey: #4a4a4a;
    --rule-grey: #c9c9c9;
    --on-teal: #ffffff;
  }
  * { margin: 0; padding: 0; box-sizing: border-box; }
  html, body { width: 1200px; height: 1200px; overflow: hidden; }
  body { background: var(--backdrop); position: relative; font-family: "Lato", sans-serif; }

  .card { position: absolute; top: 310px; width: 366px; height: 594px; text-align: center; }
  .card--front { left: 233px; background: var(--card-white); color: var(--text-grey); }
  .card--back { left: 628px; background: var(--brand-teal); color: var(--on-teal); }

  .brand-name {
    position: absolute; left: 0; right: 0; top: 440px;
    font-family: "Raleway", sans-serif; font-weight: 700; color: var(--brand-teal);
    font-size: 27px; line-height: 30px; letter-spacing: 1px; text-transform: uppercase;
  }
  .card--front .brand-name { top: 120px; }
  .sectors { position: absolute; left: 0; right: 0; top: 206px; font-size: 15px; letter-spacing: 0.2px; }

  .contact { position: absolute; left: 0; right: 0; top: 355px; }
  .person-name { font-family: "Raleway", sans-serif; font-weight: 700; font-size: 21px; color: var(--brand-teal); line-height: 24px; }
  .person-role { font-size: 17px; line-height: 22px; }
  .icon-row { display: flex; align-items: center; justify-content: center; gap: 4px; margin: 6px 0 4px; }
  .icon-row .rule { width: 36px; height: 1px; background: var(--rule-grey); margin: 0 4px; }
  .icon-badge { width: 26px; height: 26px; border: 1.5px solid var(--brand-teal); border-radius: 50%; display: flex; align-items: center; justify-content: center; }
  .contact-line { font-size: 17px; line-height: 22px; }
  .contact-line--gap { margin-bottom: 6px; }

  .card--back .brand-name { color: var(--on-teal); font-size: 40px; line-height: 44px; top: 205px; letter-spacing: 2px; }
  .services {
    position: absolute; left: 0; right: 0; top: 414px; list-style: none;
    font-family: "Raleway", sans-serif; font-weight: 600; font-size: 17.5px; line-height: 21.5px;
  }
</style>
</head>
<body>
  <section class="card card--front">
    <div class="brand-name">Harbourline<br>Electrical Solutions</div>
    <p class="sectors">COMMERCIAL INDUSTRIAL RESIDENTIAL</p>

    <div class="contact">
      <p class="person-name">MARCUS T. HOLLINGS</p>
      <p class="person-role">Project Manager</p>

      <div class="icon-row" aria-label="Social media">
        <span class="rule"></span>
        <span class="icon-badge"></span>
        <span class="icon-badge"></span>
        <span class="rule"></span>
      </div>
      <p class="contact-line contact-line--gap">@hlelectricalsolutions</p>

      <div class="icon-row">
        <span class="rule"></span>
        <span class="icon-badge" aria-label="Phone">
          <svg width="12" height="16" viewBox="0 0 12 16"><rect x="1.5" y="1" width="9" height="14" rx="1.5" fill="none" stroke="#0f5468" stroke-width="1.4"/><line x1="5" y1="12.5" x2="7" y2="12.5" stroke="#0f5468" stroke-width="1.4"/></svg>
        </span>
        <span class="icon-badge" aria-label="Email">
          <svg width="14" height="10" viewBox="0 0 14 10"><rect x="0.5" y="0.5" width="13" height="9" rx="1" fill="#0f5468"/><polyline points="1,1.2 7,5.8 13,1.2" fill="none" stroke="#fff" stroke-width="1.2"/></svg>
        </span>
        <span class="rule"></span>
      </div>
      <p class="contact-line">(441) 555-0187</p>
      <p class="contact-line">hlelectricalsolutions@mailvento.com</p>
    </div>
  </section>

  <section class="card card--back">
    <div class="brand-name">HARBOURLINE</div>
    <ul class="services">
      <li>ELECTRICAL CONSTRUCTION</li>
      <li>MAINTENANCE</li>
      <li>LED LIGHTING &amp; AUTOMATION</li>
      <li>DATA &amp; COMMUNICATION</li>
      <li>LIFE SAFETY SYSTEMS</li>
      <li>(FIRE ALARM / SECURITY)</li>
    </ul>
  </section>
</body>
</html>
```